Cover für ein Taschenbuch zum Thema Ruhestand gesucht!
Zielgruppe
Unsere Zielgruppe sind Senioren, bzw. Menschen im Alter 50+. Es handelt sich bei dem Buch um einen Ratgeber zum Thema 'Ruhestand'. Allerdings wird das Buch ebenso von einer jüngeren Zielgruppe gekauft, da der Ratgeber auch gerne an Eltern oder Großeltern verschenkt wird.
Aufgabenstellung
siehe Dateiupload
Format: 5,25' x 8'

```html
<!DOCTYPE html>
<html lang="de">
<head>
<meta charset="utf-8">
<title>Ihr Lebensabend – Buchcover</title>
<link rel="stylesheet" href="https://fonts.googleapis.com/css2?family=Cinzel:wght@400;600&family=Arvo:ital,wght@1,700&family=Crimson+Text&display=swap">
<style>
  :root {
    --page-bg: #ececec;
    --sky-top: #1f93c8;
    --sky-mid: #5bb2da;
    --sky-light: #cfe6f0;
    --sun-warm: #f6b23a;
    --sun-deep: #e2611d;
    --sand: #d7832d;
    --badge: #2a8fc3;
    --text-light: #ffffff;
    --text-dark: #1d2a33;
    --spine-shade: rgba(0, 0, 0, 0.18);
  }
  * { margin: 0; padding: 0; box-sizing: border-box; }
  html, body {
    width: 1200px;
    height: 3033px;
    overflow: hidden;
    background: var(--page-bg);
  }
  .book-cover {
    position: absolute;
    left: 150px;
    top: 831px;
    width: 900px;
    height: 1371px;
    overflow: hidden;
    background: linear-gradient(180deg, var(--sky-top) 0%, var(--sky-mid) 30%, var(--sky-light) 48%, #eaf2f2 55%);
    box-shadow: 0 20px 50px rgba(0, 0, 0, 0.25);
  }
  .cover-photo {
    position: absolute;
    left: 0;
    right: 0;
    top: 560px;
    bottom: 0;
    background:
      radial-gradient(ellipse 45% 30% at 52% 52%, #fff4c8 0%, var(--sun-warm) 40%, transparent 75%),
      linear-gradient(180deg, rgba(234, 242, 242, 0) 0%, #f3d9a6 22%, var(--sun-warm) 50%, var(--sun-deep) 75%, var(--sand) 100%);
  }
  .spine-edge {
    position: absolute;
    left: 0;
    top: 0;
    bottom: 0;
    width: 44px;
    background: linear-gradient(90deg, var(--spine-shade), rgba(255,255,255,0.12) 30%, rgba(0,0,0,0.08) 70%, transparent);
  }
  .cover-text {
    position: relative;
    text-align: center;
    padding-left: 44px;
  }
  .title {
    margin-top: 112px;
    font-family: "Cinzel", serif;
    font-weight: 600;
    font-size: 80px;
    line-height: 1;
    color: var(--text-light);
  }
  .subtitle {
    margin-top: 16px;
    font-family: "Cinzel", serif;
    font-weight: 400;
    font-size: 27px;
    letter-spacing: 0.5px;
    color: var(--text-light);
  }
  .author {
    display: inline-block;
    margin-top: 40px;
    width: 333px;
    height: 76px;
    line-height: 76px;
    background: var(--badge);
    font-family: "Arvo", serif;
    font-style: italic;
    font-weight: 700;
    font-size: 33px;
    color: var(--text-light);
  }
  .tagline {
    margin-top: 78px;
    font-family: "Crimson Text", serif;
    font-size: 42px;
    line-height: 52px;
    color: var(--text-dark);
  }
</style>
</head>
<body>
  <main class="book-cover">
    <div class="cover-photo" role="img" aria-label="Foto: älteres Paar in Liegestühlen am Strand bei Sonnenuntergang, Hand in Hand"></div>
    <div class="spine-edge"></div>
    <div class="cover-text">
      <h1 class="title">IHR LEBENSABEND</h1>
      <p class="subtitle">DAS SCHÖNSTE LIEGT NOCH VOR IHNEN!</p>
      <div class="author">Konrad Wessel</div>
      <p class="tagline">Praktische Ideen und Ratschläge, mit<br>denen Sie Ihre freien Jahre voller<br>Freude gestalten können</p>
    </div>
  </main>
</body>
</html>
```